Varko label design

Redesign cafe range label for lightly carbonated fruit sodas.
Existing label has not worked in the market place and needs to appeal to 18-40 year olds with an active healthy lifestyle.

Product will remain in current 330ml glass bottle and flavour profile will include current range, sparkling water. It is preferred to maintain a body label only but will consider neck label as well. No over cap concepts will be considered..

Attached final shows brand progress. It has lost its way and needs reinvigorating.

Reason: I have extended the deadline to get proper feed back from others on the designs. Thank you all for your submissions so far. Ned

```html
<!DOCTYPE html>
<html lang="en">
<head>
<meta charset="utf-8">
<title>Varko label range</title>
<link rel="stylesheet" href="https://fonts.googleapis.com/css2?family=Federo&family=Tinos&display=swap">
<style>
  :root {
    --ink: #111111;
    --paper: #ffffff;
    --berry: #9b30d9;
    --berry-tint: #f6f1fb;
    --berry-leaf: #3fc73a;
    --orange: #ff2a22;
    --orange-tint: #fdf3f1;
    --orange-peel: #f06a1c;
    --orange-flesh: #e8336b;
    --lemon: #ffb81f;
    --lemon-tint: #fffbea;
    --lemon-fruit: #ffd83a;
    --lemon-leaf: #3cb437;
  }
  * { margin: 0; padding: 0; box-sizing: border-box; }
  html, body { width: 1200px; height: 1000px; overflow: hidden; background: var(--paper); }
  .canvas { position: relative; width: 1200px; height: 1000px; }

  .label {
    position: absolute; top: 160px; width: 361px; height: 562px;
    border: 1.5px solid var(--ink); background: var(--paper); overflow: hidden;
  }
  .label--berry  { left: 35px; }
  .label--orange { left: 418px; }
  .label--lemon  { left: 800px; }

  .pattern { position: absolute; inset: 0; }
  .label--berry  .pattern { background: var(--berry-tint); }
  .label--orange .pattern { background: var(--orange-tint); }
  .label--lemon  .pattern { background: var(--lemon-tint); }

  .brand {
    position: absolute; top: 40px; left: 0; right: 0;
    display: flex; align-items: center; justify-content: center; gap: 8px;
    font-family: "Federo", sans-serif; font-size: 28px; color: var(--ink);
  }
  .brand-dot { width: 18px; height: 18px; border-radius: 50%; background: var(--ink); }

  .flavour {
    position: absolute; left: 0; right: 0; text-align: center;
    font-family: "Federo", sans-serif; font-size: 40px; line-height: 48px;
    color: var(--ink); letter-spacing: 0.5px;
  }
  .label--berry  .flavour { top: 132px; }
  .label--orange .flavour { top: 138px; font-size: 44px; }
  .label--lemon  .flavour { top: 146px; font-size: 42px; }

  .fruit { position: absolute; border-radius: 48%; }
  .label--berry .fruit {
    left: 100px; top: 270px; width: 162px; height: 152px;
    background: radial-gradient(circle at 65% 45%, var(--berry) 0 28%, var(--berry-leaf) 55%, #2f9e2c 100%);
  }
  .label--orange .fruit {
    left: 102px; top: 262px; width: 196px; height: 150px;
    background: radial-gradient(circle at 45% 45%, var(--orange-flesh) 0 30%, var(--orange-peel) 55%, #e64a19 100%);
  }
  .label--lemon .fruit {
    left: 84px; top: 224px; width: 196px; height: 176px;
    background: linear-gradient(100deg, var(--lemon-leaf) 0 40%, var(--lemon-fruit) 55%, #ffcc1a 100%);
  }

  .volume {
    position: absolute; top: 524px; left: 0; right: 0; text-align: center;
    font-family: "Tinos", serif; font-size: 14px; color: var(--ink);
  }
  .colour-bar { position: absolute; bottom: 0; left: 105px; width: 150px; height: 10px; }
  .label--berry  .colour-bar { background: var(--berry); }
  .label--orange .colour-bar { background: var(--orange); }
  .label--lemon  .colour-bar { background: var(--lemon); }
</style>
</head>
<body>
<main class="canvas">
  <section class="label label--berry">
    <div class="pattern" role="img" aria-label="Faint lilac pattern of raspberry sprigs"></div>
    <div class="brand"><span class="brand-dot"></span>Varko</div>
    <h2 class="flavour">RASPBERRY<br>&amp;<br>CRANBERRY</h2>
    <div class="fruit" role="img" aria-label="Illustration of a raspberry sprig with green leaves and purple berries"></div>
    <p class="volume">330ml</p>
    <div class="colour-bar"></div>
  </section>

  <section class="label label--orange">
    <div class="pattern" role="img" aria-label="Faint pink pattern of halved oranges"></div>
    <div class="brand"><span class="brand-dot"></span>Varko</div>
    <h2 class="flavour">BLOOD<br>ORANGE</h2>
    <div class="fruit" role="img" aria-label="Illustration of a halved blood orange with leaves"></div>
    <p class="volume">330ml</p>
    <div class="colour-bar"></div>
  </section>

  <section class="label label--lemon">
    <div class="pattern" role="img" aria-label="Faint yellow pattern of lemons with leaves"></div>
    <div class="brand"><span class="brand-dot"></span>Varko</div>
    <h2 class="flavour">LEMONCELLO</h2>
    <div class="fruit" role="img" aria-label="Illustration of a lemon with green leaves"></div>
    <p class="volume">330ml</p>
    <div class="colour-bar"></div>
  </section>
</main>
</body>
</html>
```